SEO Friendly Web Design Needed for Leading Software Company

Founded in 1986, TRBW is the market leader for innovative software solutions for the heavy civil construction industry. Our suite of products, including the bestsellers GroundQuote® and SiteTrack®, are used by more than 40,000 workers every day to improve their proficiency at estimating, job management, resource management, safety and equipment maintenance. TRBW also offers new mobile applications and cloud computing services so companies can work on a wide array of devices including laptops, tablets and smartphones.

In addition to high quality software, TRBW is best known for providing world-class customer service, and for its friendly, employee-ownership culture. We offer a full range of professional support options to help customers maximize their software investment including implementation planning, training and INSTANT 24/7 phone support.

Goals, objectives and target audience

The goal of our new layout and design will be to increase conversions, enhance user experience and enhance our SERP rankings.

Our objectives are as follows:
1. Clean and well laid out home page. White space is OK.
2. CTAs in strategic locations throughout to drive conversions and MQLs
3. SEO rich content with appropriate layout to meet our SEO requirements
4. 2 Master Design Templates – Home & Internal
5. Custom Design elements for individual modules

Target Audience:
- Heavy / Civil Construction Industry
- C Level executives or persons in leadership roles who utilize our software
- MEN in the construction industry.

Requirements
Should not have
• Feminine design - our industry is largely male construction workers.
Don't use script or goofy fonts
Don't change the logo, or put it in an image where it is not easily viewable.

```html
<!DOCTYPE html>
<html lang="en">
<head>
<meta charset="utf-8">
<title>TRBW – Construction Software</title>
<link href="https://fonts.googleapis.com/css2?family=Open+Sans:wght@300;400;600;700&display=swap" rel="stylesheet">
<style>
:root{
  --orange:#f39200;
  --green:#2ea84a;
  --green-dark:#1f8a38;
  --ink:#222;
  --text:#333;
  --muted:#777;
  --rule:#e3e3e3;
  --topbar:#3a3a3a;
  --grey-btn:#8a8a8a;
  --footer:#2b2b28;
}
*{box-sizing:border-box;margin:0;padding:0}
html,body{width:1200px;height:3794px;overflow:hidden}
body{position:relative;background:#fff;font-family:"Open Sans",Arial,sans-serif;color:var(--text)}
a{color:inherit;text-decoration:none}
ul{list-style:none}

.topbar{position:absolute;left:0;top:0;width:1200px;height:26px;background:var(--topbar);font-size:12px;color:var(--orange)}
.topbar .util{position:absolute;left:96px;top:5px;display:flex;gap:14px}
.topbar .contact{position:absolute;right:96px;top:5px;display:flex;gap:18px;align-items:center}
.topbar .phone{font-weight:700;font-size:14px;display:flex;gap:6px;align-items:center}

.header{position:absolute;left:0;top:26px;width:1200px;height:107px;background:#fff}
.brand{position:absolute;left:96px;top:30px;display:flex;align-items:center;gap:12px;font-size:40px;font-weight:700;color:var(--green);letter-spacing:1px}
.brand .mark{width:30px;height:30px;background:var(--green)}
.nav{position:absolute;right:96px;top:42px;display:flex;gap:28px;font-size:18px;color:#555}
.nav .active{color:var(--orange)}

.hero{position:absolute;left:0;top:133px;width:1200px;height:541px;background:linear-gradient(100deg,#1d2a3a 0%,#3a4452 35%,#6d5a2e 60%,#b08a1c 80%,#7a6220 100%)}
.hero-title{position:absolute;left:96px;top:60px;font-size:46px;font-weight:700;color:#fff;letter-spacing:-.5px}
.hero-lead{position:absolute;left:96px;top:124px;width:470px;font-size:17px;line-height:24px;color:#e2e6ea}
.hero-list{position:absolute;left:96px;top:208px;font-size:13px;font-weight:600;color:#fff}
.hero-list li{position:relative;padding-left:20px;height:31px;margin-bottom:7px}
.hero-list li::before{content:"";position:absolute;left:2px;top:2px;width:5px;height:10px;border:solid #fff;border-width:0 2px 2px 0;transform:rotate(40deg)}
.hero-cta{position:absolute;left:96px;top:397px;display:flex;gap:32px}
.btn-arrow{position:relative;display:inline-block;height:34px;line-height:34px;padding:0 36px 0 16px;background:var(--green);color:#fff;font-weight:600;font-size:16px}
.btn-arrow::after{content:"";position:absolute;right:-12px;top:0;border-left:12px solid var(--green);border-top:17px solid transparent;border-bottom:17px solid transparent}
.btn-arrow::before{content:"›";position:absolute;right:10px;top:0;font-size:18px}
.tiles{position:absolute;left:735px;top:47px;display:grid;grid-template-columns:repeat(3,100px);column-gap:32px;row-gap:8px}
.tile{height:150px;font-size:12px;line-height:14px;color:#fff}
.tile .ph{width:100px;height:100px;border:4px solid #fff;margin-bottom:4px;background:linear-gradient(135deg,#5d6b7a,#a8b2bb)}
.tile.active .ph{border-color:var(--orange);background:linear-gradient(135deg,#c08a2e,#e0b860)}

.product{position:absolute;left:0;width:1200px;height:400px}
.product .photo{position:absolute;left:102px;top:0;width:402px;height:332px;box-shadow:0 2px 6px rgba(0,0,0,.25)}
.product h2{position:absolute;left:541px;top:6px;font-size:34px;font-weight:300;color:#333;letter-spacing:-.5px}
.product.active h2{color:var(--orange)}
.features{position:absolute;left:541px;top:68px;width:566px;font-size:13px;font-weight:600;line-height:19px;color:#222}
.features li{position:relative;padding:0 0 12px 28px;margin-bottom:14px;border-bottom:1px solid var(--rule)}
.features li:last-child{border-bottom:0}
.features li::before{content:"";position:absolute;left:6px;top:2px;width:5px;height:11px;border:solid #222;border-width:0 2px 2px 0;transform:rotate(40deg)}
.actions{position:absolute;left:541px;top:294px;display:flex;gap:10px}
.btn-sm{position:relative;display:inline-block;height:22px;line-height:22px;padding:0 22px 0 9px;font-size:11px;color:#fff;background:var(--green)}
.btn-sm::after{content:"›";position:absolute;right:7px;top:-1px;font-size:13px}
.btn-sm.more{background:var(--grey-btn)}
.active .btn-sm.more{background:var(--orange)}

.to-top{position:absolute;right:0;top:1014px;width:69px;height:38px;background:#6b6b6b;color:#fff;font-size:9px;line-height:10px;padding:9px 0 0 22px}
.to-top::before{content:"";position:absolute;left:8px;top:15px;border-bottom:7px solid #fff;border-left:5px solid transparent;border-right:5px solid transparent}

.footer{position:absolute;left:0;top:3247px;width:1200px;height:496px;background:linear-gradient(180deg,#4a4a3c 0%,#2f2f29 40%,#222220 100%)}
.footer-brand{position:absolute;left:563px;top:-4px;width:74px;height:46px;background:#fff;text-align:center;line-height:46px;font-weight:700;font-size:18px;color:var(--green)}
.fcol{position:absolute;top:94px;width:170px;font-size:12px;color:#ddd}
.fcol h3{font-size:16px;font-weight:600;color:var(--orange);margin-bottom:16px}
.fcol h3.sub{margin-top:24px}
.fcol li{height:30px;line-height:29px;border-bottom:1px solid rgba(255,255,255,.12);padding-left:12px;position:relative}
.fcol li::before{content:"›";position:absolute;left:2px;top:0;color:#bbb}
.fcol li.current{background:#fff;color:var(--orange)}
.contact-list li{padding-left:24px;border-bottom:0;display:flex;gap:14px}
.contact-list li::before{content:none}
.contact-list svg{position:absolute;left:2px;top:9px}
.contact-list .addr{height:auto;line-height:17px;padding-top:6px;display:block}
.social{display:flex;gap:10px;margin-top:4px}
.social span{width:30px;height:30px;border:2px solid #ddd;border-radius:50%;display:inline-block}
.social-label{font-size:11px;color:#4aa8e0;margin:4px 0 0 40px}

.bottombar{position:absolute;left:0;top:3743px;width:1200px;height:51px;background:var(--green);color:#fff;font-size:12px;line-height:51px;padding-left:94px}
.bottombar a{margin-left:16px}
</style>
</head>
<body>

<div class="topbar">
  <nav class="util"><a href="#">Tools</a><a href="#">News</a><a href="#">Blogs</a></nav>
  <div class="contact">
    <a href="#">Contact Us</a><a href="#">Sales</a>
    <span class="phone"><svg width="12" height="12" viewBox="0 0 24 24"><path fill="#f39200" d="M6.6 10.8a15.1 15.1 0 0 0 6.6 6.6l2.2-2.2c.3-.3.7-.4 1-.2 1.1.4 2.3.6 3.6.6.6 0 1 .4 1 1V20c0 .6-.4 1-1 1A17 17 0 0 1 3 4c0-.6.4-1 1-1h3.5c.6 0 1 .4 1 1 0 1.3.2 2.5.6 3.6.1.3 0 .7-.2 1z"/></svg>1800 555 0142</span>
  </div>
</div>

<header class="header">
  <div class="brand"><span class="mark"></span>TRBW</div>
  <nav class="nav">
    <a class="active" href="#">Software</a><a href="#">Services</a><a href="#">Pricing</a><a href="#">Careers</a><a href="#">Events</a><a href="#">About Us</a>
  </nav>
</header>

<section class="hero" role="img" aria-label="Excavator on a construction site at dusk">
  <h1 class="hero-title">Construction Software</h1>
  <p class="hero-lead">The Industry leader in Construction Software that can manage your projects from start to finish</p>
  <ul class="hero-list">
    <li>Lorem ipsum dolor sit amet, consectetur sed eiusmod incididunt</li>
    <li>Lorem ipsum dolor sit amet, consectetur adipisicing elit eiusmod tempor</li>
    <li>Amet, consectetur adipisicing elit, lorem ipsum dolor sit amet</li>
    <li>Consectetur sed eiusmod incididunt lorem ipsum consectetur sed</li>
  </ul>
  <div class="hero-cta"><a class="btn-arrow" href="#">Contact Sales</a><a class="btn-arrow" href="#">View Demo</a></div>
  <div class="tiles">
    <div class="tile active"><div class="ph" role="img" aria-label="Estimator on site"></div>Estimating &amp; Bidding</div>
    <div class="tile"><div class="ph" role="img" aria-label="Managers on site"></div>Job Management</div>
    <div class="tile"><div class="ph" role="img" aria-label="Driver in a truck"></div>Dispatching &amp; Scheduling</div>
    <div class="tile"><div class="ph" role="img" aria-label="Worker in safety gear"></div>Safety Management</div>
    <div class="tile"><div class="ph" role="img" aria-label="Survey equipment"></div>GPS</div>
    <div class="tile"><div class="ph" role="img" aria-label="Tools"></div>Equipment Maintenance</div>
    <div class="tile"><div class="ph" role="img" aria-label="Fuel tank"></div>Fuel Tracking</div>
    <div class="tile"><div class="ph" role="img" aria-label="Mobile devices"></div>Mobile Apps</div>
    <div class="tile"><div class="ph" role="img" aria-label="Building site"></div>Keyword Text Link</div>
  </div>
</section>

<section class="product active" style="top:735px">
  <div class="photo" role="img" aria-label="Engineer with plans beside an excavator" style="background:linear-gradient(160deg,#8fb3d6 0%,#c9a43a 55%,#4a4a48 100%)"></div>
  <h2>Estimating &amp; Bidding</h2>
  <ul class="features">
    <li>Lorem ipsum dolor sit amet, consectetur adipisicing elit, sed do eiusmod tempor incididunt</li>
    <li>Lorem ipsum dolor sit amet, consectetur adipisicing elit,</li>
    <li>Lorem ipsum dolor sit amet, consectetur adipisicing elit, sed do eiusmod tempor incididunt</li>
    <li>Sed do eiusmod tempor incididunt ut labore et dolore magna aliqua</li>
  </ul>
  <div class="actions"><a class="btn-sm" href="#">Contact Sales</a><a class="btn-sm more" href="#">Read More</a></div>
</section>

<section class="product" style="top:1151px">
  <div class="photo" role="img" aria-label="Managers in hard hats on a building site" style="background:linear-gradient(160deg,#c8ccd0 0%,#6b7078 50%,#2a2c30 100%)"></div>
  <h2>Job Management</h2>
  <ul class="features">
    <li>Lorem ipsum dolor sit amet, consectetur adipisicing elit, sed do eiusmod tempor incididunt</li>
    <li>Lorem ipsum dolor sit amet, consectetur adipisicing elit,</li>
    <li>Lorem ipsum dolor sit amet, consectetur adipisicing elit, sed do eiusmod tempor incididunt</li>
    <li>Sed do eiusmod tempor incididunt ut labore et dolore magna aliqua</li>
  </ul>
  <div class="actions"><a class="btn-sm" href="#">Contact Sales</a><a class="btn-sm more" href="#">Read More</a></div>
</section>

<section class="product" style="top:1567px">
  <div class="photo" role="img" aria-label="Driver in a work truck" style="background:linear-gradient(160deg,#eef0f2 0%,#b9c6d2 50%,#6a7a8c 100%)"></div>
  <h2>Dispatching &amp; Scheduling</h2>
  <ul class="features">
    <li>Lorem ipsum dolor sit amet, consectetur adipisicing elit, sed do eiusmod tempor incididunt</li>
    <li>Lorem ipsum dolor sit amet, consectetur adipisicing elit,</li>
    <li>Lorem ipsum dolor sit amet, consectetur adipisicing elit, sed do eiusmod tempor incididunt</li>
    <li>Sed do eiusmod tempor incididunt ut labore et dolore magna aliqua</li>
  </ul>
  <div class="actions"><a class="btn-sm" href="#">Contact Sales</a><a class="btn-sm more" href="#">Read More</a></div>
</section>

<section class="product" style="top:1983px">
  <div class="photo" role="img" aria-label="Worker in hard hat and gloves" style="background:linear-gradient(160deg,#3b7cc4 0%,#6fa2d8 45%,#b04a2a 100%)"></div>
  <h2>Safety Management</h2>
  <ul class="features">
    <li>Lorem ipsum dolor sit amet, consectetur adipisicing elit, sed do eiusmod tempor incididunt</li>
    <li>Lorem ipsum dolor sit amet, consectetur adipisicing elit,</li>
    <li>Lorem ipsum dolor sit amet, consectetur adipisicing elit, sed do eiusmod tempor incididunt</li>
    <li>Sed do eiusmod tempor incididunt ut labore et dolore magna aliqua</li>
  </ul>
  <div class="actions"><a class="btn-sm" href="#">Contact Sales</a><a class="btn-sm more" href="#">Read More</a></div>
</section>

<section class="product" style="top:2399px">
  <div class="photo" role="img" aria-label="Hand tools arranged on white" style="background:linear-gradient(160deg,#ffffff 0%,#e8e2d6 55%,#b8a070 100%)"></div>
  <h2>Equipment Maintenance</h2>
  <ul class="features">
    <li>Lorem ipsum dolor sit amet, consectetur adipisicing elit, sed do eiusmod tempor incididunt</li>
    <li>Lorem ipsum dolor sit amet, consectetur adipisicing elit,</li>
    <li>Lorem ipsum dolor sit amet, consectetur adipisicing elit, sed do eiusmod tempor incididunt</li>
    <li>Sed do eiusmod tempor incididunt ut labore et dolore magna aliqua</li>
  </ul>
  <div class="actions"><a class="btn-sm" href="#">Contact Sales</a><a class="btn-sm more" href="#">Read More</a></div>
</section>

<section class="product" style="top:2815px">
  <div class="photo" role="img" aria-label="Survey instrument on a tripod in a field" style="background:linear-gradient(180deg,#2f5f9a 0%,#6d95c4 55%,#9a7a4a 100%)"></div>
  <h2>GPS</h2>
  <ul class="features">
    <li>Lorem ipsum dolor sit amet, consectetur adipisicing elit, sed do eiusmod tempor incididunt</li>
    <li>Lorem ipsum dolor sit amet, consectetur adipisicing elit,</li>
    <li>Lorem ipsum dolor sit amet, consectetur adipisicing elit, sed do eiusmod tempor incididunt</li>
    <li>Sed do eiusmod tempor incididunt ut labore et dolore magna aliqua</li>
  </ul>
  <div class="actions"><a class="btn-sm" href="#">Contact Sales</a><a class="btn-sm more" href="#">Read More</a></div>
</section>

<a class="to-top" href="#">BACK<br>TO TOP</a>

<footer class="footer" role="img" aria-label="Dim construction site background">
  <div class="footer-brand">TRBW</div>

  <div class="fcol" style="left:94px">
    <h3>Softwares</h3>
    <ul>
      <li>GroundQuote®</li><li class="current">SiteTrack®</li><li>Safety Application</li><li>RouteBoard</li><li>GPS</li><li>Fleet Circle</li><li>TankLog</li><li>workrecord.example</li><li>Mobile Apps</li><li>Mobile Apps</li>
    </ul>
  </div>

  <div class="fcol" style="left:304px">
    <h3>Serices</h3>
    <ul><li>Could Services</li><li>Custom Programming</li><li>Universities</li><li>Instant Support</li></ul>
    <h3 class="sub">Training &amp; Events</h3>
    <ul><li>Training Options</li><li>Dummy Links Plz Ad</li></ul>
  </div>

  <div class="fcol" style="left:513px">
    <h3>News</h3>
    <ul><li>Newsroom</li><li>Newsletter</li><li>Press Kit</li><li>Newsletter Subscription</li></ul>
    <h3 class="sub">Careers</h3>
    <ul><li>Careers At TRBW</li><li>Careers in Construction</li></ul>
  </div>

  <div class="fcol" style="left:722px">
    <h3>About Us</h3>
    <ul><li>About TRBW</li><li>TRBW Culture Blog</li><li>Our Clients</li><li>Contact/More Info</li><li>The TRBW Story</li><li>Map &amp; Directions</li><li>Stability</li><li>Why Choose TRBW</li></ul>
  </div>

  <div class="fcol" style="left:924px;width:200px">
    <h3>Contact Us</h3>
    <ul class="contact-list">
      <li><svg width="10" height="10" viewBox="0 0 24 24"><path fill="#ddd" d="M6.6 10.8a15.1 15.1 0 0 0 6.6 6.6l2.2-2.2c.3-.3.7-.4 1-.2 1.1.4 2.3.6 3.6.6.6 0 1 .4 1 1V20c0 .6-.4 1-1 1A17 17 0 0 1 3 4c0-.6.4-1 1-1h3.5c.6 0 1 .4 1 1 0 1.3.2 2.5.6 3.6.1.3 0 .7-.2 1z"/></svg>Sales :<span>800-555-0131</span></li>
      <li><svg width="10" height="10" viewBox="0 0 24 24"><path fill="#ddd" d="M6.6 10.8a15.1 15.1 0 0 0 6.6 6.6l2.2-2.2c.3-.3.7-.4 1-.2 1.1.4 2.3.6 3.6.6.6 0 1 .4 1 1V20c0 .6-.4 1-1 1A17 17 0 0 1 3 4c0-.6.4-1 1-1h3.5c.6 0 1 .4 1 1 0 1.3.2 2.5.6 3.6.1.3 0 .7-.2 1z"/></svg>Support :<span>800-555-0177</span></li>
      <li><svg width="11" height="9" viewBox="0 0 22 16"><rect x="1" y="1" width="20" height="14" fill="none" stroke="#ddd" stroke-width="2"/><path d="M1 1l10 8 10-8" fill="none" stroke="#ddd" stroke-width="2"/></svg>Email :<span>info@trbw.example</span></li>
      <li class="addr"><svg width="10" height="13" viewBox="0 0 20 26"><path fill="#ddd" d="M10 0a10 10 0 0 0-10 10c0 7 10 16 10 16s10-9 10-16A10 10 0 0 0 10 0zm0 14a4 4 0 1 1 0-8 4 4 0 0 1 0 8z"/></svg>4820 W. Granite Blvd.<br>Stone Ridge, TX 77000</li>
    </ul>
    <h3 class="sub">Social Media</h3>
    <div class="social"><span></span><span></span><span></span><span></span><span></span></div>
    <div class="social-label">Follow us</div>
  </div>
</footer>

<div class="bottombar">All Right Reserved © Copyright with www.trbw.example - 2012<a href="#">Terms</a><a href="#">Privacy Policy</a></div>

</body>
</html>
```